Web design for small empirical brand consulting company that will sell a web-based brand tool

We need a totally new and very appealing website:
Purpose: We want to attract lots of potential customers with this website... especially, we want to sell our web-based tool valuquant®... we want to be perceived as innovative, trendy, but solid and reliable… we want customers go to the website, login at „valuquant®“ (see structure), and perceive how it works.. and the contacting us or in the near future being able to buy a login and work with the tool… so we want to a) inform (on the website or send the url to customers) and b) to „force“ potential customers getting in contact with us…
Structure (e.g.): Must Home, valuquant®, About us, Contact (incl. legal notice); we are open for more, Nice to have e.g. references/clients, press... for example, we publish a nice book in a couple of months and might want to show it somewhere on the website as well...)
Layout: We would like to have more/mainly figures - may be animated or something like that – in specific those on slides 7 and 8 as well as 6 and 9 (which would be for our web-based tool valuquant®...)... excellent, but simple and with few text…
Fonts: Eurostile; CMYK 100/23/100/19, CMYK 0/0/0/70
Logo: Would you please use the lorentavo-logo used in this file?
Social Media: we think that it might make sense to be connected to chatterbay, quipline and so on as well…
Phantasy: May be it is possible to have something between a classic marketing research and an e-commerce website... just a thought... because it is mainly about the new tool that will be assessable through a login... but customers might want to contact us or vice versa in order to check how the tool will work (btw: you do not have further info about valuquant® here... I know)… I dream of having a site where people go to and by components of our tool like at brimbo… click and buy and go for it…
It is possible to program it in php or java? Thanks.
Pages I personally like: Don’t know if that helps, but I personally like those websites just they seem so simple: http:// www.pellivarn.com/, http://www.craftelune.net/... but I am veeery open
Pages I do not like anymore: my own www.lorentavo.ch

```html
<!DOCTYPE html>
<html lang="en">
<head>
<meta charset="utf-8">
<title>lorentavo – Simply measuring and modeling your brand success</title>
<link rel="stylesheet" href="https://fonts.googleapis.com/css2?family=Roboto:wght@300;400;500;700&display=swap">
<style>
:root{
  --green:#1d7a3c;
  --ink:#4d4d4d;
  --ink-soft:#777;
  --line:#d6d6d6;
  --band:#e7e7e7;
  --dark:#5b5b5b;
  --white:#fff;
}
*{box-sizing:border-box;margin:0;padding:0}
html,body{width:1200px;height:2788px;overflow:hidden}
body{font-family:"Roboto",Arial,sans-serif;color:var(--ink);background:var(--white);font-size:14px;line-height:1.45}
a{text-decoration:none}
.btn{display:inline-block;background:var(--green);color:var(--white);font-size:11px;font-weight:700;letter-spacing:.5px;padding:7px 14px;text-transform:uppercase}
.btn--ghost{background:rgba(255,255,255,.85);color:var(--ink);border:1px solid #999}

/* header */
.site-header{height:100px;display:flex;align-items:center;justify-content:space-between;padding:0 70px}
.brand{display:flex;align-items:center;gap:12px;font-size:30px;font-weight:500;color:var(--ink)}
.brand__mark{width:24px;height:24px;background:var(--green)}
.main-nav{display:flex;gap:4px}
.main-nav a{font-size:12px;font-weight:500;color:var(--ink);padding:9px 14px;text-transform:uppercase}
.main-nav a.is-active{background:var(--green);color:var(--white)}

/* hero */
.hero{position:relative;height:540px;background:linear-gradient(180deg,#c5ccd2 0%,#dfe3e6 45%,#9aa3aa 75%,#6f777d 100%);text-align:center}
.hero__title{position:absolute;top:220px;left:0;right:0;font-size:30px;font-weight:400;line-height:1.2;color:#2f2f2f;text-transform:uppercase}
.hero__cta{position:absolute;top:305px;left:50%;transform:translateX(-50%)}
.hero__arrows{position:absolute;top:360px;left:50%;transform:translateX(-50%);display:flex;gap:4px}
.hero__arrows span{width:26px;height:26px;background:var(--white);display:flex;align-items:center;justify-content:center}

/* intro */
.intro{height:360px;padding:40px 140px 0}
.intro__title{text-align:center;font-size:17px;font-weight:700;text-transform:uppercase;line-height:1.35;margin-bottom:40px}
.features{display:grid;grid-template-columns:1fr 1fr;column-gap:60px;row-gap:22px;list-style:none}
.features li{display:flex;gap:16px;font-size:15px;align-items:flex-start}
.features b{flex:none;width:26px;height:26px;background:var(--green);color:var(--white);font-size:13px;display:flex;align-items:center;justify-content:center}

/* team */
.team{height:380px;background:var(--band);text-align:center}
.section-tab{display:inline-block;border:1px solid #aaa;border-top:none;background:var(--white);font-size:13px;font-weight:700;padding:8px 40px;text-transform:uppercase;color:var(--green)}
.team__list{display:flex;justify-content:center;gap:80px;margin-top:28px;list-style:none}
.team__photo{width:90px;height:108px;margin:0 auto 10px;background:linear-gradient(180deg,#b9b9b9,#8a8a8a)}
.team__name{font-size:12px}
.team__quote{margin-top:22px;font-size:14px;line-height:1.7}
.team .btn{margin-top:16px}

/* offer columns */
.offers{height:400px;display:grid;grid-template-columns:repeat(3,1fr);gap:30px;padding:24px 60px 0}
.offer__label{font-size:14px;font-weight:700;color:var(--green);text-transform:uppercase;margin-bottom:6px}
.offer__media{height:160px;margin-bottom:14px}
.offer__media--a{background:linear-gradient(135deg,#6d7f91,#c8d2da)}
.offer__media--b{background:linear-gradient(135deg,#c9c4b8,#7b7367)}
.offer__media--c{background:linear-gradient(135deg,#474a52,#a3a7ad)}
.offer p{font-size:13px;color:var(--ink-soft);margin-bottom:12px}

/* benefits */
.benefits{height:620px;background:var(--dark);display:grid;grid-template-columns:repeat(4,1fr);grid-template-rows:1fr 1fr;padding:30px 70px}
.benefit{text-align:center;color:var(--white);padding:20px 28px}
.benefit h3{font-size:16px;font-weight:500;margin-bottom:16px}
.benefit__icon{width:70px;height:70px;border-radius:50%;border:2px solid var(--white);margin:0 auto 16px;display:flex;align-items:center;justify-content:center}
.benefit p{font-size:12px;color:#ddd;margin-bottom:14px}

/* tool */
.tool{height:260px;display:flex;gap:50px;padding:30px 70px}
.tool__media{flex:none;width:480px;height:200px;background:linear-gradient(180deg,#f1f1f1,#cfd6d2);border:1px solid var(--line)}
.tool h2{font-size:22px;font-weight:700;line-height:1.25;color:#333;margin-bottom:12px}
.tool p{font-size:12px;color:var(--ink-soft);margin-bottom:14px}

/* footer */
.site-footer{height:128px;background:var(--band);padding:18px 70px 0;position:relative;font-size:12px}
.footer__top{display:flex;justify-content:space-between}
.footer__address{font-style:normal}
.footer__social{text-align:right}
.footer__social div{display:flex;gap:6px;justify-content:flex-end;margin-top:8px}
.footer__social span{width:22px;height:22px;background:var(--green)}
.footer__bottom{position:absolute;left:70px;right:70px;bottom:12px;text-align:center;font-size:11px;color:var(--ink-soft)}
</style>
</head>
<body>

<header class="site-header">
  <div class="brand"><span class="brand__mark"></span>lorentavo</div>
  <nav class="main-nav">
    <a class="is-active" href="#">Home</a>
    <a href="#">valuquant®</a>
    <a href="#">About us</a>
    <a href="#">Contact</a>
  </nav>
</header>

<section class="hero" role="img" aria-label="Businessman leaping above a city skyline under a pale sky">
  <h1 class="hero__title">Simply measuring and modeling<br>your brand success</h1>
  <a class="btn btn--ghost hero__cta" href="#">Read more ›</a>
  <div class="hero__arrows">
    <span><svg width="10" height="10" viewBox="0 0 10 10"><path d="M7 1 3 5l4 4" fill="none" stroke="#333" stroke-width="2"/></svg></span>
    <span><svg width="10" height="10" viewBox="0 0 10 10"><path d="M3 1l4 4-4 4" fill="none" stroke="#333" stroke-width="2"/></svg></span>
  </div>
</section>

<section class="intro">
  <h2 class="intro__title">Lorentavo Ltd., a spin-off company from the University of Lindenfeld,<br>specialized in empirical brand consulting.</h2>
  <ol class="features">
    <li><b>1</b>Testing your brand using scientifically developed tools.</li>
    <li><b>4</b>Development and implementation of strategies for your whole company, your products/services as well as your CEO.</li>
    <li><b>2</b>Detailed examination of your marketing and communication procedures.</li>
    <li><b>5</b>Cost optimization of your marketing and communication budgets by as much as 30%.</li>
    <li><b>3</b>Generating long-term effects thanks to a modeling and calculation of your brand success.</li>
  </ol>
</section>

<section class="team">
  <span class="section-tab">About us</span>
  <ul class="team__list">
    <li><div class="team__photo" role="img" aria-label="Portrait of Tobias Renner"></div><p class="team__name">Tobias Renner, Dr.</p></li>
    <li><div class="team__photo" role="img" aria-label="Portrait of Frieder Aldsen"></div><p class="team__name">Frieder Aldsen, M.A.</p></li>
    <li><div class="team__photo" role="img" aria-label="Portrait of Martin Veltz"></div><p class="team__name">Martin Veltz, Dr. des.</p></li>
    <li><div class="team__photo" role="img" aria-label="Portrait of Kevin Strohm"></div><p class="team__name">Kevin Strohm, M.A.*</p></li>
  </ul>
  <p class="team__quote">A strong brand has a direct impact on the company's success (Varo, Lind, 2003).<br>Strong brands account for over 30% of the market capitalization of Marlowe &amp; Crane's 500 firms (Pellham, 2013).</p>
  <a class="btn" href="#">Read more</a>
</section>

<section class="offers">
  <article class="offer">
    <h3 class="offer__label">Company brand</h3>
    <div class="offer__media offer__media--a" role="img" aria-label="Modern office towers seen from below"></div>
    <p>Using our unique, scientifically tested instruments, valuquant® measures and models your brand.</p>
    <a class="btn" href="#">Read more</a>
  </article>
  <article class="offer">
    <h3 class="offer__label">Company brand</h3>
    <div class="offer__media offer__media--b" role="img" aria-label="Team of colleagues in a meeting"></div>
    <p>Using our unique, scientifically tested instruments, valuquant® measures and models your brand.</p>
    <a class="btn" href="#">Read more</a>
  </article>
  <article class="offer">
    <h3 class="offer__label">CEO brand</h3>
    <div class="offer__media offer__media--c" role="img" aria-label="Executive in a dark business suit"></div>
    <p>Using our unique, scientifically tested instruments, valuquant® measures and models your brand.</p>
    <a class="btn" href="#">Read more</a>
  </article>
</section>

<section class="benefits">
  <div class="benefit"><h3>Metrics</h3><div class="benefit__icon"><svg width="34" height="30" viewBox="0 0 34 30"><path d="M3 28h28M6 26V16M13 26V9M20 26V13M27 26V4" stroke="#fff" stroke-width="3" fill="none"/></svg></div><p>You receive precise data for your brand perception and your target groups.</p><a class="btn" href="#">Read more</a></div>
  <div class="benefit"><h3>Trend Models</h3><div class="benefit__icon"><svg width="34" height="30" viewBox="0 0 34 30"><path d="M2 26 12 15l7 6L31 5M24 5h7v7" stroke="#fff" stroke-width="3" fill="none"/></svg></div><p>You receive precise models of how your brand will develop over time.</p><a class="btn" href="#">Read more</a></div>
  <div class="benefit"><h3>Precision</h3><div class="benefit__icon"><svg width="34" height="34" viewBox="0 0 34 34"><circle cx="17" cy="17" r="14" stroke="#fff" stroke-width="3" fill="none"/><circle cx="17" cy="17" r="7" stroke="#fff" stroke-width="3" fill="none"/><circle cx="17" cy="17" r="2" fill="#fff"/></svg></div><p>You receive exact figures backed by empirical and tested methods.</p><a class="btn" href="#">Read more</a></div>
  <div class="benefit"><h3>Cost Reduction</h3><div class="benefit__icon"><svg width="34" height="30" viewBox="0 0 34 30"><path d="M2 4l10 11 7-6 12 16M24 25h7v-7" stroke="#fff" stroke-width="3" fill="none"/></svg></div><p>You reduce your marketing and communication budget by up to 30%.</p><a class="btn" href="#">Read more</a></div>
  <div class="benefit"><h3>Clearness</h3><div class="benefit__icon"><svg width="36" height="24" viewBox="0 0 36 24"><path d="M2 12C8 3 28 3 34 12 28 21 8 21 2 12z" stroke="#fff" stroke-width="3" fill="none"/><circle cx="18" cy="12" r="4" fill="#fff"/></svg></div><p>You receive clear results that are easy to read and to share.</p><a class="btn" href="#">Read more</a></div>
  <div class="benefit"><h3>Security</h3><div class="benefit__icon"><svg width="28" height="32" viewBox="0 0 28 32"><rect x="3" y="14" width="22" height="16" fill="#fff"/><path d="M8 14V9a6 6 0 0 1 12 0v5" stroke="#fff" stroke-width="3" fill="none"/></svg></div><p>Your data are stored safely and remain fully confidential with us.</p><a class="btn" href="#">Read more</a></div>
  <div class="benefit"><h3>Fit</h3><div class="benefit__icon"><svg width="32" height="26" viewBox="0 0 32 26"><path d="M3 13l9 9L29 4" stroke="#fff" stroke-width="4" fill="none"/></svg></div><p>You receive solutions that fit your company and your brand goals.</p><a class="btn" href="#">Read more</a></div>
  <div class="benefit"><h3>Customer loyalty</h3><div class="benefit__icon"><svg width="32" height="28" viewBox="0 0 32 28"><path d="M16 26 4 14a7 7 0 0 1 12-9 7 7 0 0 1 12 9z" stroke="#fff" stroke-width="3" fill="none"/></svg></div><p>You learn how to keep your customers loyal to your brand longer.</p><a class="btn" href="#">Read more</a></div>
</section>

<section class="tool">
  <div class="tool__media" role="img" aria-label="Laptop and tablet showing the valuquant® dashboard"></div>
  <div>
    <h2>valuquant® – the web-based tool that measures, models and manages your brand online</h2>
    <p>Log in to valuquant® and see how your brand performs. The tool collects data on brand perception, turns it into clear figures and models the long-term effect of every marketing decision. Choose the modules you need, test them with your own data and contact us at any time to find the package that fits your company and your budget.</p>
    <a class="btn" href="#">Read more</a>
  </div>
</section>

<footer class="site-footer">
  <div class="footer__top">
    <address class="footer__address">Sonnfeldstrasse 14, 8010 Lindenfeld<br>Tel: +41 00 555 01 20 | Fax: +41 00 555 01 21<br>info@lorentavo.ch</address>
    <div class="footer__social">Connect with us
      <div><span aria-label="chatterbay"></span><span aria-label="quipline"></span><span aria-label="network"></span><span aria-label="video"></span></div>
    </div>
  </div>
  <p class="footer__bottom">Home | valuquant® | About us | Contact | Terms and Conditions | Privacy Policy<br>Copyright ©2014 All Rights Reserved</p>
</footer>

</body>
</html>
```